Business Card Design

We are a manufacturing and distribution company with most of our customer base being supermarkets. We have established brand guidelines that are attached.

```html
<!DOCTYPE html>
<html lang="en">
<head>
<meta charset="utf-8">
<title>Corvane Business Card</title>
<link rel="stylesheet" href="https://fonts.googleapis.com/css2?family=Poppins:wght@400;600;700&display=swap">
<style>
  :root {
    --bg: #0e0e0f;
    --card: #232427;
    --card-back: #1f2022;
    --edge-blue: #0a67c2;
    --brand-blue: #1677cf;
    --brand-red: #e0242b;
    --text-light: #e6e6e6;
    --text-muted: #c9c9cb;
    --rule: #4a4b4f;
    --emboss: #2c2d30;
  }
  * { box-sizing: border-box; margin: 0; padding: 0; }
  html, body { width: 1200px; height: 820px; overflow: hidden; }
  body {
    background: var(--bg);
    font-family: "Poppins", sans-serif;
    display: flex;
    align-items: center;
    justify-content: center;
    gap: 50px;
  }
  .card {
    width: 525px;
    height: 300px;
    position: relative;
    border-left: 3px solid var(--edge-blue);
    border-bottom: 3px solid var(--edge-blue);
    box-shadow: 0 14px 40px rgba(0,0,0,.6);
  }
  .card--front { background: var(--card); color: var(--text-light); }
  .card--back { background: var(--card-back); display: flex; align-items: center; justify-content: center; }

  .brand {
    position: absolute;
    top: 58px;
    right: 48px;
    display: flex;
    align-items: center;
    gap: 12px;
  }
  .brand__square { width: 22px; height: 22px; background: var(--brand-blue); }
  .brand__name { font-weight: 700; font-size: 34px; letter-spacing: 2px; color: #fff; line-height: 1; }

  .rule-top {
    position: absolute;
    top: 150px;
    left: 40px;
    right: 40px;
    height: 1px;
    background: var(--rule);
  }

  .person { position: absolute; left: 40px; top: 172px; }
  .person__name { font-weight: 600; font-size: 19px; letter-spacing: .5px; line-height: 1.1; }
  .person__first { color: var(--brand-red); }
  .person__last { color: var(--brand-blue); }
  .person__role { font-size: 13px; color: var(--text-muted); margin-top: 2px; }
  .person__rule { width: 160px; height: 1px; background: var(--rule); margin: 9px 0 8px; }

  .contact { list-style: none; font-size: 12.5px; color: var(--text-muted); }
  .contact li { display: flex; align-items: center; gap: 8px; line-height: 1.5; }
  .contact svg { width: 12px; height: 12px; flex: none; }

  .address {
    position: absolute;
    right: 40px;
    top: 190px;
    text-align: right;
    font-size: 12.5px;
    color: var(--text-muted);
    line-height: 1.45;
  }

  .back-mark {
    font-weight: 700;
    font-size: 56px;
    letter-spacing: 6px;
    color: var(--emboss);
    text-shadow: 0 1px 0 rgba(255,255,255,.04);
  }
</style>
</head>
<body>
  <section class="card card--front" aria-label="Business card front">
    <div class="brand">
      <span class="brand__square"></span>
      <span class="brand__name">CORVANE</span>
    </div>
    <div class="rule-top"></div>

    <div class="person">
      <p class="person__name"><span class="person__first">DANIEL</span> <span class="person__last">HARTLEY</span></p>
      <p class="person__role">Managing Director</p>
      <div class="person__rule"></div>
      <ul class="contact">
        <li>
          <svg viewBox="0 0 24 24" fill="none" stroke="var(--brand-red)" stroke-width="2.4"><path d="M5 3h4l2 5-2.5 1.5a11 11 0 0 0 6 6L16 13l5 2v4a2 2 0 0 1-2 2A17 17 0 0 1 3 5a2 2 0 0 1 2-2z"/></svg>
          044-310 872 615
        </li>
        <li>
          <svg viewBox="0 0 24 24" fill="none" stroke="var(--brand-red)" stroke-width="2.4"><rect x="2" y="5" width="20" height="14"/><path d="M2 5l10 8 10-8"/></svg>
          hello@corvane.com
        </li>
        <li>
          <svg viewBox="0 0 24 24" fill="none" stroke="var(--brand-red)" stroke-width="2.2"><circle cx="12" cy="12" r="10"/><path d="M2 12h20M12 2a15 15 0 0 1 0 20M12 2a15 15 0 0 0 0 20"/></svg>
          www.corvane.com
        </li>
      </ul>
    </div>

    <p class="address">88, Millbrook Trade Park<br>30218, Eastfield</p>
  </section>

  <section class="card card--back" aria-label="Business card back">
    <span class="back-mark">CORVANE</span>
  </section>
</body>
</html>
```